A website for a Maltese Law Firm

Our law firm needs a website to further its business. The site should have a simple yet effective design. We would need the following sections: About us, Practice Areas, About Malta, Contact. These should be further split as follows:

About us: Our firm, Our values, What others say, Offices

Practice Areas: Crimimal, Citizenship & Residence, Sovereign Patron Pathway, Criminal Defence, Civil Litigation, Arbitration and ADR, Commercial and Corporate, Media Law.

About Malta: just one section.

Contact: Just one section

We would also need a news feed at the front of the site to include latest news regarding our cases.

At the bottom we need a section for our Terms and a Privacy Statement.

Our logo is being attached.

Target Market(s)

All clients looking for legal assistance in Malta

Industry/Entity Type

Legal

Coding

Coded - Design and coding required

Number of Pages Required

1 page

Requirements
Must have
• It must be simple yet striking.

```html
<!DOCTYPE html>
<html lang="en">
<head>
<meta charset="utf-8">
<title>Bellanti &amp; Mizzi Advocates</title>
<link href="https://fonts.googleapis.com/css2?family=Cinzel:wght@400;600&family=Lato:ital,wght@0,400;0,700;1,400&display=swap" rel="stylesheet">
<style>
:root{
  --ink:#2b2d33;
  --ink-soft:#3a3c42;
  --text:#333;
  --mist:#ededed;
  --band:#a9aaae;
  --base:#c8c9cd;
  --line:#d4d4d4;
  --white:#fff;
}
*{box-sizing:border-box;margin:0;padding:0}
html,body{width:1200px;height:2723px;overflow:hidden}
body{font-family:'Lato',sans-serif;color:var(--text);background:var(--white);position:relative}
section,header,nav,footer{position:absolute;left:0;width:1200px}
.abs{position:absolute}

/* header */
.site-header{top:0;height:105px;background:var(--white)}
.brand-name{font-family:'Cinzel',serif;font-weight:400;white-space:nowrap}
.brand{left:72px;top:32px;font-size:27px;line-height:40px;color:var(--ink)}
.contact-top{left:897px;top:24px;font-size:16px;font-weight:700;color:var(--ink)}
.contact-top div{display:flex;align-items:center;gap:10px;height:34px}
.contact-top svg{width:24px;height:24px}

/* nav */
.main-nav{top:105px;height:46px;background:var(--ink);display:flex;padding-left:67px}
.main-nav a{display:block;height:46px;line-height:46px;padding:0 22px;font-family:'Cinzel',serif;font-size:15px;color:var(--white);text-decoration:none;border-right:1px solid #55575d}
.main-nav a.active{background:#9c9da1;color:var(--ink)}

/* hero */
.hero{top:151px;height:426px;background:linear-gradient(180deg,#4a3328 0%,#8a6a55 40%,#6b3a22 75%,#3a1c10 100%)}
.hero-photo{position:absolute;inset:0}
.hero-title{left:181px;top:470px;font-family:'Cinzel',serif;font-size:29px;line-height:36px;color:#f3ead9;text-shadow:0 2px 4px rgba(0,0,0,.6)}
.btn-dark{background:var(--ink);color:var(--white);font-family:'Cinzel',serif;border:1px solid #8a8b90}
.hero-cta{left:726px;top:490px;width:290px;height:49px;font-size:20px;line-height:47px;text-align:center}
.chev{position:absolute;width:24px;height:90px}

/* welcome */
.welcome{top:577px;height:454px;background:var(--mist)}
h2.welcome-title{left:69px;top:60px;font-family:'Cinzel',serif;font-weight:400;font-size:31px;color:var(--ink)}
.lead{left:69px;top:113px;width:680px;font-size:16.5px;line-height:24px;color:#222}
.body-copy{left:69px;top:178px;width:680px;font-size:13.5px;line-height:22.5px;color:#333}
.pill{display:flex;align-items:center;height:30px}
.pill span{background:#b3b4b8;border:1px solid #777;height:28px;line-height:26px;padding:0 12px 0 8px;font-size:11px;text-transform:uppercase;color:var(--ink);font-weight:700}
.pill i{display:block;width:32px;height:32px;border-radius:50%;background:var(--ink);margin-left:-10px;position:relative}
.pill i:after{content:"";position:absolute;left:11px;top:11px;width:8px;height:8px;border-top:2px solid #fff;border-right:2px solid #fff;transform:rotate(45deg)}
.read-more{left:69px;top:358px}
.eval-box{left:797px;top:62px;width:330px;height:325px;border:2px solid var(--ink-soft);padding:22px 17px}
.eval-box h3{font-family:'Cinzel',serif;font-weight:400;font-size:24px;color:var(--ink);margin-bottom:22px}
.field{background:var(--white);border:1px solid #ccc;height:40px;font-size:12px;padding:10px 10px;color:#444;margin-bottom:9px}
.field.tall{height:76px}
.eval-box .pill{margin-top:14px}
.eval-box .pill span{font-size:14px;height:34px;line-height:32px;padding:0 20px 0 12px}
.eval-box .pill i{width:38px;height:38px}
.eval-box .pill i:after{left:13px;top:14px}

/* practice */
.practice{top:1031px;height:423px;background:var(--white)}
.section-title{width:1200px;text-align:center;font-family:'Cinzel',serif;font-weight:400;font-size:29px;color:var(--ink)}
.practice .section-title{top:55px}
.area{top:123px;width:270px;text-align:center}
.area-icon{width:100px;height:100px;margin:0 auto;border:3px solid var(--ink);display:flex;align-items:center;justify-content:center}
.area-icon.on{background:var(--ink)}
.area-icon svg{width:54px;height:54px}
.area h4{font-family:'Cinzel',serif;font-weight:400;font-size:20px;color:var(--ink);margin-top:20px;letter-spacing:.5px}
.area p{font-size:13.5px;line-height:18px;margin:10px auto 0;width:200px}
.area .plus{font-size:15px;margin-top:12px}

/* cases */
.cases{top:1454px;height:524px;background:var(--mist)}
.cases .section-title{top:55px}
.case{top:121px;width:309px}
.case-frame{height:164px;border:1px solid #bbb;background:var(--white);padding:8px;position:relative}
.case-photo{height:146px}
.date{position:absolute;left:16px;top:16px;width:48px;font-weight:700;text-align:center}
.date b{display:block;background:var(--ink);color:#fff;font-size:17px;line-height:25px}
.date span{display:block;background:#fff;color:#222;font-size:14px;line-height:20px;font-weight:400}
.case h5{font-size:13.5px;font-weight:700;margin-top:14px;color:#111}
.case p{font-size:12.5px;line-height:19px;margin-top:9px;color:#333}
.case .more{font-size:12px;margin-top:10px;color:#222}
.view-all{left:537px;top:450px}
.view-all span{width:100px;text-align:center}

/* testimonials */
.testimonials{top:1978px;height:302px;background:var(--white)}
.testimonials .section-title{top:58px}
.client-photo{left:134px;top:120px;width:116px;height:118px;background:linear-gradient(180deg,#dfe3e8,#b9c0c8 55%,#2c2f3a)}
.quote{left:354px;top:124px;width:720px;font-style:italic;font-size:13.5px;line-height:22px;color:#333}
.quote-mark{font-family:Georgia,serif;font-size:60px;color:#ddd;line-height:1}
.quote-end{font-family:Georgia,serif;font-style:normal;font-size:40px;color:#ddd;line-height:0;vertical-align:-14px;margin-left:4px}
.client-name{left:308px;top:222px;font-family:'Cinzel',serif;font-size:19px;color:var(--ink);letter-spacing:1px}

/* cta */
.cta{top:2280px;height:130px;background:var(--band)}
.cta-text{left:116px;top:40px;font-family:'Cinzel',serif;font-size:29px;line-height:37px;color:var(--white)}
.cta-btn{left:844px;top:41px;width:225px;height:48px;background:var(--ink);color:#fff;border:1px solid #ddd;font-size:22px;font-weight:700;text-align:center;line-height:46px}

/* footer */
.site-footer{top:2410px;height:267px;background:var(--ink);color:#fff}
.foot-head{font-family:'Cinzel',serif;font-size:17px;letter-spacing:.5px;padding-bottom:8px;border-bottom:1px solid #555}
.quick{left:67px;top:44px;width:140px}
.quick ul{list-style:none;margin-top:10px}
.quick li{font-size:12px;line-height:24.5px;padding-left:14px;position:relative}
.quick li:before{content:"";position:absolute;left:2px;top:10px;width:4px;height:4px;background:#fff;border-radius:50%}
.contacts-col{left:302px;top:44px;width:490px}
.map{left:303px;top:86px;width:258px;height:125px;background:linear-gradient(135deg,#e8e6df,#d5dcc9 50%,#e3e0d6)}
.addr{left:590px;top:88px;font-size:12px;line-height:17px}
.addr div{display:flex;gap:12px;margin-bottom:9px}
.addr svg{width:13px;height:15px;flex:none;margin-top:1px}
.foot-brand{left:870px;top:96px;width:275px;text-align:center;font-size:17px;line-height:24px;color:var(--white)}
.social{left:926px;top:153px;display:flex;gap:16px}
.social span{width:30px;height:30px;border-radius:50%;border:2px solid #fff}
.social .s1{background:#3b5998}.social .s2{background:#0e76a8}.social .s3{background:#2aa9e0}.social .s4{background:#dd4b39}

.base{top:2677px;height:46px;background:var(--base);font-size:12.5px;color:#333}
.base .left{left:69px;top:15px}
.base .right{right:69px;top:15px}
</style>
</head>
<body>

<header class="site-header">
  <div class="abs brand brand-name">Bellanti &amp; Mizzi Advocates</div>
  <div class="abs contact-top">
    <div><svg viewBox="0 0 24 24"><rect x="1" y="1" width="22" height="22" rx="4" fill="#2b2d33"/><rect x="8" y="5" width="8" height="14" rx="1.5" fill="none" stroke="#fff" stroke-width="1.8"/></svg>555-210-4471</div>
    <div><svg viewBox="0 0 24 24"><rect x="1" y="1" width="22" height="22" rx="4" fill="#2b2d33"/><rect x="5" y="7" width="14" height="10" fill="none" stroke="#fff" stroke-width="1.6"/><path d="M5 7l7 6 7-6" fill="none" stroke="#fff" stroke-width="1.6"/></svg>info@bmadvocates.com</div>
  </div>
</header>

<nav class="main-nav">
  <a class="active">Home</a><a>About Malta</a><a>Practice Areas</a><a>Our Firm</a><a>Our Values</a><a>What Others Say</a><a>Contact Us</a>
</nav>

<section class="hero">
  <div class="hero-photo" role="img" aria-label="Photo of a man's clenched fists in handcuffs resting on a polished wooden table"></div>
  <svg class="chev" style="left:28px;top:170px" viewBox="0 0 24 90"><path d="M20 2L4 45l16 43" fill="none" stroke="#eee" stroke-width="2"/></svg>
  <svg class="chev" style="left:1148px;top:170px" viewBox="0 0 24 90"><path d="M4 2l16 43L4 88" fill="none" stroke="#eee" stroke-width="2"/></svg>
</section>
<div class="abs hero-title">Realize Your Constitutional<br>Right For Qualified Legal Help</div>
<div class="abs btn-dark hero-cta">Get A Free Consultation</div>

<section class="welcome">
  <h2 class="abs welcome-title">Welcome To Bellanti &amp; Mizzi Advocates</h2>
  <p class="abs lead">Lorem ipsum dolor sit amet, consectetuer adipiscing elit, sed diam nonummy nibh euismod tincidunt ut laoreet dolore magna aliquam erat volutpat.</p>
  <p class="abs body-copy">Lorem ipsum dolor sit amet, consectetur adipiscing elit. Sed vitae magna tellus. Aenean ante nunc, semper nec cursus non, rutrum ac eros. Vestibulum mattis justo ac dui bibendum consequat a ac ipsum. Praesent a arcu venenatis, auctor velit eu, suscipit libero. Quisque convallis, leo ac pharetra sagittis, ipsum arcu auctor urna, sit amet cursus risus augue in eros. Duis lacinia nisi vitae leo commodo, non finibus magna maximus. Sed posuere, neque eget bibendum pulvinar, ligula erat suscipit dolor, ut maximus arcu mi et tortor. Quisque imperdiet turpis et ligula mollis ultricies. Mauris lacinia rhoncus odio, at rutrum diam mollis eu. Quisque ut ipsum faucibus, tristique dui vitae, posuere orci.</p>
  <div class="abs pill read-more"><span>Read More</span><i></i></div>
  <form class="abs eval-box">
    <h3>Free Case Evaluation</h3>
    <div class="field">Name</div>
    <div class="field">Email</div>
    <div class="field tall">Message</div>
    <div class="pill"><span>Submit</span><i></i></div>
  </form>
</section>

<section class="practice">
  <h2 class="abs section-title">Our Practice Areas</h2>
  <svg class="chev" style="left:28px;top:200px;height:60px" viewBox="0 0 24 60"><path d="M18 2L5 30l13 28" fill="none" stroke="#555" stroke-width="1.5"/></svg>
  <svg class="chev" style="left:1148px;top:200px;height:60px" viewBox="0 0 24 60"><path d="M6 2l13 28L6 58" fill="none" stroke="#555" stroke-width="1.5"/></svg>
  <div class="abs area" style="left:65px">
    <div class="area-icon"><svg viewBox="0 0 54 54"><circle cx="16" cy="32" r="9" fill="none" stroke="#2b2d33" stroke-width="5"/><circle cx="38" cy="32" r="9" fill="none" stroke="#2b2d33" stroke-width="5"/><path d="M20 22l7-6 7 6" fill="none" stroke="#2b2d33" stroke-width="3"/></svg></div>
    <h4>Crimimal</h4>
    <p>Lorem ipsum dolor sit amet, consectetuer Lorem dolor sit amet, consectetuer</p>
    <div class="plus">[+]</div>
  </div>
  <div class="abs area" style="left:324px">
    <div class="area-icon on"><svg viewBox="0 0 54 54"><rect x="13" y="7" width="28" height="40" rx="2" fill="#fff"/><circle cx="27" cy="22" r="7" fill="none" stroke="#2b2d33" stroke-width="2"/><path d="M20 22h14M27 15v14" stroke="#2b2d33" stroke-width="1.5"/><rect x="20" y="36" width="14" height="3" fill="#2b2d33"/></svg></div>
    <h4>Citizenship &amp; Residence</h4>
    <p>Lorem ipsum dolor sit amet, consectetuer Lorem dolor sit amet, consectetuer</p>
    <div class="plus">[+]</div>
  </div>
  <div class="abs area" style="left:595px">
    <div class="area-icon"><svg viewBox="0 0 54 54"><circle cx="27" cy="15" r="8" fill="#2b2d33"/><rect x="13" y="24" width="28" height="22" rx="3" fill="#2b2d33"/><rect x="6" y="29" width="42" height="11" fill="#fff" stroke="#2b2d33" stroke-width="2"/><path d="M10 34h34" stroke="#2b2d33" stroke-width="2"/></svg></div>
    <h4>Criminal Defence</h4>
    <p>Lorem ipsum dolor sit amet, consectetuer Lorem dolor sit amet, consectetuer</p>
    <div class="plus">[+]</div>
  </div>
  <div class="abs area" style="left:867px">
    <div class="area-icon"><svg viewBox="0 0 54 54"><rect x="22" y="6" width="14" height="22" transform="rotate(45 29 17)" fill="#2b2d33"/><path d="M25 24L12 37" stroke="#2b2d33" stroke-width="5"/><rect x="8" y="42" width="30" height="5" fill="#2b2d33"/></svg></div>
    <h4>Civil Litigation</h4>
    <p>Lorem ipsum dolor sit amet, consectetuer Lorem dolor sit amet, consectetuer</p>
    <div class="plus">[+]</div>
  </div>
</section>

<section class="cases">
  <h2 class="abs section-title">Case Studies</h2>
  <article class="abs case" style="left:69px">
    <div class="case-frame"><div class="case-photo" role="img" aria-label="Photo of leather-bound law books on a shelf" style="background:linear-gradient(90deg,#3a2416,#8a5a2e 30%,#5a3a1e 60%,#9a7040)"></div>
      <div class="date"><b>06</b><span>Jun</span></div></div>
    <h5>Lorem Ipsum Dolor Sit Amet &nbsp;Consectetur</h5>
    <p>Lorem ipsum dolor sit amet, consectetur adipiscing elit. Sed vitae magna tellus. Aenean ante nunc, semper nec cursus non, rutrum ac eros.</p>
    <div class="more">Read More &rsaquo;&rsaquo;</div>
  </article>
  <article class="abs case" style="left:445px">
    <div class="case-frame"><div class="case-photo" role="img" aria-label="Photo of a handcuffed man standing in a courtroom" style="background:linear-gradient(90deg,#3a1e14,#6a3a24 40%,#2a2a2e 70%,#4a3a34)"></div>
      <div class="date"><b>06</b><span>Jun</span></div></div>
    <h5>Lorem Ipsum Dolor Sit Amet &nbsp;Consectetur</h5>
    <p>Lorem ipsum dolor sit amet, consectetur adipiscing elit. Sed vitae magna tellus. Aenean ante nunc, semper nec cursus non, rutrum ac eros.</p>
    <div class="more">Read More &rsaquo;&rsaquo;</div>
  </article>
  <article class="abs case" style="left:819px">
    <div class="case-frame"><div class="case-photo" role="img" aria-label="Photo of hands signing a document with a pen" style="background:linear-gradient(120deg,#3a3a40,#d8d4cc 45%,#f0ede8 70%,#b8b0a6)"></div>
      <div class="date"><b>07</b><span>Jun</span></div></div>
    <h5>Lorem Ipsum Dolor Sit Amet &nbsp;Consectetur</h5>
    <p>Lorem ipsum dolor sit amet, consectetur adipiscing elit. Sed vitae magna tellus. Aenean ante nunc, semper nec cursus non, rutrum ac eros.</p>
    <div class="more">Read More &rsaquo;&rsaquo;</div>
  </article>
  <div class="abs pill view-all"><span>View All</span><i></i></div>
</section>

<section class="testimonials">
  <h2 class="abs section-title">Client Testimonials</h2>
  <svg class="chev" style="left:28px;top:175px;height:60px" viewBox="0 0 24 60"><path d="M18 2L5 30l13 28" fill="none" stroke="#555" stroke-width="1.5"/></svg>
  <svg class="chev" style="left:1148px;top:175px;height:60px" viewBox="0 0 24 60"><path d="M6 2l13 28L6 58" fill="none" stroke="#555" stroke-width="1.5"/></svg>
  <div class="abs client-photo" role="img" aria-label="Portrait photo of the client in a suit"></div>
  <div class="abs quote-mark" style="left:308px;top:108px">&ldquo;</div>
  <p class="abs quote">Lorem ipsum dolor sit amet, consectetuer adipiscing elit, sed diam nonummy nibh euismod tincidunt ut laoreet dolore magna aliquam erat volutpat. Ut wisi enim ad minim veniam, quis nostrud exerci iriure dolor in Lorem ipsum dolor sit amet, consectetuer adipiscing elit, sed diam nonummy nibh euismod tincidunt ut laoreet dolore magna aliquam erat volutpat. Ut wisi enim ad minim veniam, quis nostrud exerci iriure dolo.<span class="quote-end">&rdquo;</span></p>
  <div class="abs client-name">- Adrian Falzon</div>
</section>

<section class="cta">
  <div class="abs cta-text">For Any Legal Problem, We Can Help You<br>Anytime take An Appointment Now</div>
  <div class="abs cta-btn">CONTACT US</div>
</section>

<footer class="site-footer">
  <div class="abs quick">
    <div class="foot-head">Quick Links</div>
    <ul><li>Home</li><li>About Malta</li><li>Practice Areas</li><li>Our Firm</li><li>Our Values</li><li>What Others Say</li><li>Contact Us</li></ul>
  </div>
  <div class="abs contacts-col"><div class="foot-head">Contact Details</div></div>
  <div class="abs map" role="img" aria-label="Street map showing the office location"></div>
  <div class="abs addr">
    <div><svg viewBox="0 0 13 15"><path d="M6.5 1a4.5 4.5 0 0 0-4.5 4.5C2 9 6.5 14 6.5 14S11 9 11 5.5A4.5 4.5 0 0 0 6.5 1z" fill="#fff"/><circle cx="6.5" cy="5.5" r="1.6" fill="#2b2d33"/></svg><span>Bellanti &amp; Mizzi Advocates<br>12/4, Harbour Lane, Valletta<br>88, Orchard Street, Birkirkara</span></div>
    <div><svg viewBox="0 0 13 15"><path d="M2 2l3-1 2 4-2 1.5c.8 1.8 2 3 3.5 3.5L10 8l3 2-1 3C7 13 2 8 2 2z" fill="#fff"/></svg><span>555-210-447</span></div>
    <div><svg viewBox="0 0 13 15"><rect x="1" y="5" width="11" height="6" fill="#fff"/><rect x="3" y="2" width="7" height="3" fill="#fff"/><rect x="3" y="9" width="7" height="4" fill="#fff" stroke="#2b2d33"/></svg><span>555-210-447</span></div>
    <div><svg viewBox="0 0 13 15"><rect x="1" y="4" width="11" height="8" fill="#fff"/><path d="M1 4l5.5 4L12 4" fill="none" stroke="#2b2d33"/></svg><span>info@bmadvocates.com</span></div>
  </div>
  <div class="abs foot-brand brand-name">Bellanti &amp; Mizzi Advocates</div>
  <div class="abs social"><span class="s1"></span><span class="s2"></span><span class="s3"></span><span class="s4"></span></div>
</footer>

<section class="base">
  <div class="abs left">Copyright &copy; 2016 <b>Bellanti &amp; Mizzi Advocates</b>. All Rights Reserved.</div>
  <div class="abs right">Terms &amp; Conditions &nbsp;|&nbsp; Privacy Policy &nbsp;|&nbsp; Disclaimer</div>
</section>

</body>
</html>
```